Computer Service Provider in Need of New Letterhead Design

We are BrackenLoop Computer Services, a computer/IT services company that provides IT Support, software, hardware, virus monitoring, etc. in Vermont. We are looking for new letterhead, that is both professional and matches the current theme of our business cards & website.
Please note that we want to include the following information:
www.BrackenLoop.example
802-471-3926
742 Hollis Meadow Lane, Alder Falls, VT 05498
Proactive Solutions • Approachable People • Proven Performance
I will be attaching our logo along with the business card images.
We would love to have the

```html
<!DOCTYPE html>
<html lang="en">
<head>
<meta charset="utf-8">
<title>BrackenLoop Computer Services – Letterhead</title>
<link href="https://fonts.googleapis.com/css2?family=Lato:wght@400;700&family=Tinos:wght@400;700&display=swap" rel="stylesheet">
<style>
  :root {
    --brand-blue: #2b5b82;
    --brand-orange: #f39a1e;
    --paper: #fbfbfb;
    --ink: #1a1a1a;
    --muted-ink: #4a4a4a;
    --backdrop: #7a7a7a;
  }
  * { margin: 0; padding: 0; box-sizing: border-box; }
  html, body { width: 1200px; height: 1200px; overflow: hidden; }
  body { background: var(--backdrop); position: relative; }

  .letterhead {
    position: absolute; left: 219px; top: 30px;
    width: 762px; height: 1140px;
    background: var(--paper);
    overflow: hidden;
  }
  .corner-accent { position: absolute; left: 0; top: 0; }

  .brand {
    position: absolute; right: 68px; top: 130px;
    display: flex; align-items: center; gap: 14px;
  }
  .brand-square { width: 76px; height: 76px; background: var(--brand-blue); }
  .brand-name {
    font-family: "Lato", sans-serif; font-weight: 700;
    font-size: 29px; line-height: 1.12; color: var(--brand-blue);
  }

  .letter {
    position: absolute; left: 69px; width: 624px;
    font-family: "Tinos", serif; font-size: 15.5px; line-height: 18px;
    color: var(--ink);
  }
  .letter p { text-align: justify; }
  .letter sup { font-size: 9px; line-height: 0; vertical-align: 6px; }
  .issue-date { top: 264px; }
  .recipient { top: 338px; }
  .subject { top: 449px; font-weight: 700; }
  .salutation { top: 523px; }
  .body-one { top: 560px; }
  .body-two { top: 634px; }
  .acknowledge { top: 707px; }
  .closing { top: 781px; }

  .taglines {
    position: absolute; left: 66px; top: 998px;
    list-style: none;
    font-family: "Lato", sans-serif; font-size: 15.5px; line-height: 19px;
    color: var(--ink);
  }
  .taglines li::before {
    content: ""; display: inline-block; width: 5px; height: 5px;
    border-radius: 50%; background: var(--brand-orange);
    margin-right: 7px; vertical-align: middle;
  }

  .contact {
    position: absolute; right: 30px; top: 1017px;
    font-family: "Lato", sans-serif; font-size: 13.5px; color: var(--muted-ink);
    text-align: right;
  }
  .contact-row { display: flex; align-items: center; justify-content: flex-end; gap: 5px; height: 19px; }

  .address-band {
    position: absolute; left: 0; bottom: 0; width: 100%; height: 55px;
    background: var(--brand-blue);
    display: flex; align-items: center; justify-content: center;
    font-family: "Lato", sans-serif; font-size: 16px; color: #ffffff;
  }
</style>
</head>
<body>
  <main class="letterhead">
    <svg class="corner-accent" width="230" height="230" viewBox="0 0 230 230" aria-hidden="true">
      <polygon points="0,0 220,0 0,220" fill="var(--brand-blue)"/>
      <line x1="222" y1="0" x2="0" y2="222" stroke="var(--brand-orange)" stroke-width="5"/>
    </svg>

    <header class="brand">
      <div class="brand-square"></div>
      <div class="brand-name">BrackenLoop<br>Computer Services</div>
    </header>

    <div class="letter issue-date">Issuing date: May 5, 2012</div>
    <div class="letter recipient">Name of employee: Mr. xyz<br>Address of employee<br>address line 2</div>
    <div class="letter subject">Ref: Promotion as an Assistant secretary</div>
    <div class="letter salutation">Dear Mr. xyz,</div>
    <div class="letter body-one"><p>I have the pleasure to inform you that you have been promoted as assistant secretary in the share department of the company. You are required to take charge of the new assignment on 15<sup>th</sup> May, 2012. Please accept my hearty congratulations on your promotion.</p></div>
    <div class="letter body-two"><p>Your salary scale in the promoted cadre will be Tk. 16,000 and from 15th may, your basic salary will be fixed at Tk. 12,000 in the said scale. You will be entitled to all other allowances as applicable to the staff-II of the company. Other services conditions remain unchanged.</p></div>
    <div class="letter acknowledge">Please acknowledge receipt of this letter.</div>
    <div class="letter closing">Yours sincerely,</div>

    <ul class="taglines">
      <li>Proactive Solutions</li>
      <li>Approachable People</li>
      <li>Proven Performance</li>
    </ul>

    <div class="contact">
      <div class="contact-row">802-471-3926
        <svg width="18" height="18" viewBox="0 0 18 18" aria-hidden="true">
          <circle cx="9" cy="9" r="9" fill="var(--brand-blue)"/>
          <path d="M5 6.5c0-1 1.8-1.8 4-1.8s4 .8 4 1.8l-1.4.6-.6-1.2H7l-.6 1.2z" fill="#fff"/>
          <rect x="5.5" y="8" width="7" height="5" rx="1" fill="#fff"/>
        </svg>
      </div>
      <div class="contact-row">www.BrackenLoop.example
        <svg width="18" height="18" viewBox="0 0 18 18" aria-hidden="true">
          <circle cx="9" cy="9" r="9" fill="var(--brand-blue)"/>
          <circle cx="9" cy="9" r="4.5" fill="none" stroke="#fff" stroke-width="1.4"/>
          <path d="M9 4.5v9M4.5 9h9" stroke="#fff" stroke-width="1"/>
        </svg>
      </div>
    </div>

    <footer class="address-band">742 Hollis Meadow Lane, Alder Falls, VT 05498</footer>
  </main>
</body>
</html>
```